Basic / Quick Business Card

Quick easy design project!

Need a one sided basic business card that matches font & style of brand and bottle label for our gourmet condiment, Brindle Harrow Sauce. Brindle Harrow Sauce is sold in specialty retail, gourmet groceries and appears on chef-driven restaurant menus, so the target market is a high end, gourmet, artisan-made food-loving customer.

Files Included:
Sauce Bottle Label
Brindle Harrow Sauce Round Logos

**About the logos - the logo may be used in a circle or alone vertically as on side of the bottle label**

Layout of Card:
May be vertical or horizontal based on designer ideas.

Logo usage (in circle vs. stand alone vertical logo) is up to designers descretion as well.

Reverse side of business card will be various high end / professional product photos / food shots using us.kelbo.com system. **Designer on this project will NOT design a reserve for the card.**

Paper that will be used for printing:
Kelbo Standard - it's a WHITE paper, but we use a cream background on Brindle Harrow Sauce branding, so please take this into account on design to stay brand consistent.

Elements & Copy for Card:
1. Logo in either script horizontal or vertical version
2. Copy: "Artisan Made - Small Batch"
3. Name - Wes Dorrance
4. Title - Creator
5. Phone - xxx.xxx.xxxx
6. xxxx@brindleharrow.com
7. URL: brindleharrowsauce.com
8. Social Media: @getbrindleharrow on Quillo / Pagora / Lumigrid

Please provide final files in Illustrator or InDesign format.

```html
<!DOCTYPE html>
<html lang="en">
<head>
<meta charset="utf-8">
<title>Brindle Harrow Sauce – Business Card</title>
<link href="https://fonts.googleapis.com/css2?family=Rokkitt:wght@300;400;800&display=swap" rel="stylesheet">
<style>
  :root {
    --backdrop: #d9d4cb;
    --card-black: #211f1f;
    --gold: #f0a800;
    --cream: #f4f2df;
    --ink: #1e1c1c;
  }
  * { margin: 0; padding: 0; box-sizing: border-box; }
  html, body { width: 1200px; height: 1019px; overflow: hidden; }
  body {
    background: var(--backdrop);
    font-family: "Rokkitt", serif;
    display: flex; align-items: center; justify-content: center;
  }
  .card {
    position: relative;
    width: 520px; height: 910px;
    background: var(--card-black);
    box-shadow: 0 12px 30px rgba(0,0,0,.25);
    overflow: hidden;
  }
  .tagline {
    position: absolute; top: 58px; left: 0; right: 0;
    text-align: center; color: var(--gold);
    font-size: 36px; font-weight: 400; letter-spacing: 1px;
  }
  .brand {
    position: absolute; top: 190px; left: 0; right: 0;
    display: flex; align-items: center; justify-content: center; gap: 14px;
  }
  .brand-dot {
    width: 22px; height: 22px; border-radius: 50%;
    background: var(--gold); flex: none;
  }
  .brand-name {
    color: var(--cream); font-size: 40px; font-weight: 800;
    line-height: 1; letter-spacing: .5px; white-space: nowrap;
  }
  .name-band {
    position: absolute; top: 310px; left: 0; right: 0; height: 190px;
    background: var(--gold);
  }
  .person {
    position: absolute; top: 370px; left: 0; right: 0; text-align: center;
  }
  .person-name { color: var(--ink); font-size: 44px; font-weight: 800; line-height: 1; letter-spacing: .5px; }
  .person-title { color: var(--cream); font-size: 40px; font-weight: 300; line-height: 1.05; letter-spacing: 1px; }
  .contact {
    position: absolute; top: 545px; left: 0; right: 0;
    text-align: center; color: var(--cream);
  }
  .contact-icons { display: flex; justify-content: center; gap: 14px; margin-bottom: 10px; }
  .contact-line { font-size: 30px; font-weight: 400; line-height: 1.15; letter-spacing: .5px; }
  .social-networks {
    margin-top: 14px; color: var(--gold);
    font-size: 26px; font-weight: 800; letter-spacing: 1px;
  }
  .social-handle { font-size: 30px; line-height: 1.2; letter-spacing: .5px; }
</style>
</head>
<body>
  <main class="card">
    <p class="tagline">Artisan Made - Small Batch</p>

    <div class="brand">
      <span class="brand-dot"></span>
      <span class="brand-name">Brindle Harrow Sauce</span>
    </div>

    <div class="name-band"></div>

    <div class="person">
      <p class="person-name">Wes Dorrance</p>
      <p class="person-title">Creator</p>
    </div>

    <div class="contact">
      <div class="contact-icons">
        <svg class="icon-phone" width="36" height="28" viewBox="0 0 36 28" aria-label="Phone">
          <path d="M2 10 Q18 -2 34 10 L34 14 L26 14 L25 9 Q18 6 11 9 L10 14 L2 14 Z" fill="var(--gold)"/>
          <rect x="8" y="16" width="20" height="10" rx="2" fill="var(--gold)"/>
          <circle cx="18" cy="21" r="3" fill="var(--card-black)"/>
        </svg>
        <svg class="icon-mail" width="32" height="28" viewBox="0 0 32 28" aria-label="Email">
          <path d="M2 12 L16 2 L30 12 L30 26 L2 26 Z" fill="var(--gold)"/>
          <path d="M2 12 L16 20 L30 12" fill="none" stroke="var(--card-black)" stroke-width="2"/>
        </svg>
        <svg class="icon-web" width="30" height="30" viewBox="0 0 30 30" aria-label="Website">
          <circle cx="15" cy="15" r="13" fill="var(--gold)"/>
          <g fill="none" stroke="var(--card-black)" stroke-width="1.6">
            <ellipse cx="15" cy="15" rx="6" ry="13"/>
            <line x1="2" y1="15" x2="28" y2="15"/>
            <line x1="15" y1="2" x2="15" y2="28"/>
            <path d="M4 9 H26 M4 21 H26"/>
          </g>
        </svg>
      </div>
      <p class="contact-line">555.0142.7788</p>
      <p class="contact-line">wes@brindleharrow.com</p>
      <p class="contact-line">brindleharrowsauce.com</p>
      <p class="social-networks">Pagora · Quillo · Lumigrid</p>
      <p class="social-handle">@getbrindleharrow</p>
    </div>
  </main>
</body>
</html>
```